Elegant and modern Wedding Photography brochure

My existing brochure (attached) needs a major facelift. This is one of the main selling tools - it gets emailed to my clients when they make an equiry on what packages i offer and it is printed out and walked through at our first meeting. This brochure is as critical as my website - it needs to sing!

I'm looking for an eye-catching design that says:
Elegant
Modern
Clean
Crisp
Not cutesy or lovey-dovey thanks - we are more sophisticated and professional than that.

Update images to some of the latest weddings I've shot also. Let me know files and resolution you need. I've enabled right-click to download images on my site for a limited time. Please note that I retain copyright and will pursue any breeches.

Http://www.sarahkelbrin.com/Melbourne-wedding-photography
Updates

Thanks for all of your designs! Will take a few days to decide.

Target Market(s)

Australian Women aged 24-44

Industry/Entity Type

Wedding

Font styles to use
Other font styles liked:
• Century Gothic

Requirements
Must have
• Easy to print - does not have to be 6 A4 pages like the existing brochure
Nice to have
• Some full page images - The photos are supposed to be the hero here :-)
Should not have
• Not cutesy or lovey-dovey thanks - we are more sophisticated and professional than that.

No black backgrounds, I prefer a white thanks

No images in organic shaped boxes (like the rectangles in the logo - no thanks).
Keep the lines straight and sharp

```html
<!DOCTYPE html>
<html lang="en">
<head>
<meta charset="utf-8">
<title>Sarah Kelbrin Wedding Photography Brochure</title>
<link href="https://fonts.googleapis.com/css2?family=Didact+Gothic&display=swap" rel="stylesheet">
<style>
:root{
  --stage:#000;
  --paper:#fff;
  --rose:#e8697a;
  --mint:#86cda6;
  --mint-deep:#6fbf95;
  --mint-pale:#a9dbbd;
  --sage:#6d7b6a;
  --butter:#f2e38e;
  --plum:#8a4a8e;
  --ink:#6f6f6f;
  --ink-soft:#8c8c8c;
}
*{box-sizing:border-box;margin:0;padding:0}
html,body{width:1200px;height:1000px;overflow:hidden;background:var(--stage)}
body{position:relative;font-family:"Didact Gothic",sans-serif;color:var(--ink)}
.page{position:absolute;width:438px;height:310px;background:var(--paper);overflow:hidden}
.abs{position:absolute}
.photo{position:absolute}
.page-num{position:absolute;font-size:40px;line-height:1;color:var(--mint-pale)}

/* cover */
.cover{left:68px;top:28px}
.cover .hero{left:0;top:0;width:438px;height:204px;background:linear-gradient(120deg,#6b5a3a,#c9b59a 45%,#e7ddd2 55%,#7b6c52)}
.brand-mark{left:208px;top:244px;width:22px;height:22px;border:2px solid var(--plum)}
.brand-name{left:0;width:438px;top:276px;text-align:center;font-size:11px;color:var(--plum)}
.tagline{left:0;width:438px;top:293px;text-align:center;font-size:12.5px;color:var(--mint-deep)}

/* approach */
.approach{left:663px;top:28px}
.approach .portrait{left:26px;top:29px;width:51px;height:47px;background:linear-gradient(#9a9a9a,#3e3e3e)}
.approach .accent{left:13px;top:76px;width:14px;height:24px;background:var(--butter)}
.approach h2{left:113px;top:23px;font-weight:400;font-size:17px;color:var(--rose)}
.approach h3{left:113px;top:42px;font-weight:400;font-size:13.5px;color:var(--mint-deep)}
.col{position:absolute;top:60px;font-size:5.6px;line-height:1.45;text-align:justify;color:var(--ink-soft)}
.col h4{font-weight:400;font-size:6.5px;color:var(--rose);margin-bottom:3px}
.col h4.later{margin-top:6px}
.col p+p{margin-top:4px}
.approach .rings{left:0;top:210px;width:384px;height:100px;background:linear-gradient(90deg,#e9efe6,#5a5f58 45%,#2b2d2a 60%,#cfd6cc)}
.approach .tab{left:384px;top:210px;width:54px;height:100px;background:var(--mint)}
.approach .page-num{right:6px;bottom:4px;color:#fff;font-size:36px}

/* testimonials */
.reviews{left:68px;top:347px}
.tile{position:absolute;background:linear-gradient(135deg,#8c7f6e,#d8cfc2)}
.reviews .num-block{left:14px;top:16px;width:64px;height:62px;background:var(--butter)}
.reviews .num-block span{position:absolute;left:4px;top:-2px;font-size:32px;color:#fff}
.quote-panel{position:absolute;left:82px;top:83px;width:270px;height:132px;background:var(--mint);color:#fff;padding:12px 10px}
.quote-panel h2{font-weight:400;font-size:20px;margin-bottom:10px}
.quote-panel p{font-size:6px;line-height:1.5}
.quote-panel cite{display:block;text-align:right;font-style:normal;font-size:6px;margin:2px 0 9px}

/* packages */
.packages{left:663px;top:347px}
.packages .band{left:0;top:0;width:438px;height:38px;background:var(--butter);color:#fff;font-size:18px;text-align:center;line-height:42px}
.pkg{position:absolute;top:38px;width:146px}
.pkg .shot{height:97px;background:linear-gradient(160deg,#5f6b46,#a8a88c 50%,#efeee8 70%,#4d5239)}
.pkg .label{height:13px;color:#fff;font-size:8px;text-align:center;line-height:14px}
.pkg .price{font-size:6.5px;color:var(--rose);padding:4px 0 0 24px}
.pkg .cover-hrs{font-size:5.6px;padding:2px 0 2px 24px;color:var(--ink-soft)}
.pkg ul{list-style:none;padding:0 8px 0 24px;font-size:5.3px;line-height:1.35;color:var(--ink-soft)}
.pkg li{position:relative;margin-bottom:3.2px}
.pkg li::before{content:"";position:absolute;left:-6px;top:2px;width:2px;height:2px;background:var(--rose)}
.pkg li.accent{color:var(--rose)}
.packages .note{left:160px;top:292px;font-size:4.6px;color:var(--mint-deep)}
.packages .page-num{right:2px;bottom:0}

/* a la carte */
.extras{left:68px;top:664px}
.extras .page-num{left:2px;top:0}
.fee-list{position:absolute;left:22px;top:30px;width:180px;text-align:center;font-size:5.3px;line-height:1.62;color:var(--ink-soft)}
.fee-list .item{color:var(--rose)}
.fee-list .gap{margin-top:4px}
.extras .bouquet{left:210px;top:0;width:228px;height:310px;background:linear-gradient(#f6f3ee,#e9c9cc 40%,#d9a8b0 55%,#b7c6b3 80%,#dad5cf)}
.extras .label{left:210px;top:254px;width:222px;height:20px;background:var(--mint);color:#fff;font-size:11px;text-align:center;line-height:21px}

/* contact */
.contact{left:663px;top:664px}
.contact .still{left:0;top:0;width:204px;height:310px;background:linear-gradient(#2a2a2a,#8a8a8a 55%,#dedede 80%,#9d9d9d)}
.contact h2{left:204px;width:234px;top:40px;text-align:center;font-weight:400;font-size:11px;line-height:1.3;color:var(--rose)}
.contact .copy{left:244px;width:154px;top:78px;text-align:center;font-size:6.4px;line-height:1.45;color:var(--ink-soft)}
.contact .copy p+p{margin-top:8px}
.contact .details{left:204px;top:188px;width:234px;height:66px;background:var(--mint);color:#fff;text-align:center;padding-top:8px;font-size:10px;line-height:1.25}
.contact .details .url{font-size:12px}
.contact .mark{left:279px;top:268px;width:13px;height:13px;border:1.5px solid var(--plum)}
.contact .brand{left:298px;top:268px;font-size:11px;color:var(--plum)}
</style>
</head>
<body>

<section class="page cover">
  <div class="photo hero" role="img" aria-label="Smiling bride in veil, outdoor portrait"></div>
  <div class="abs brand-mark"></div>
  <div class="abs brand-name">Sarah Kelbrin</div>
  <div class="abs tagline">Your Story. Your Photographer.</div>
</section>

<section class="page approach">
  <div class="photo portrait" role="img" aria-label="Black and white portrait of the photographer"></div>
  <div class="abs accent"></div>
  <h2 class="abs">Sarah's approach…</h2>
  <h3 class="abs">Enjoy your special day!</h3>
  <div class="col" style="left:113px;width:74px">
    <h4>Style &amp; Approach</h4>
    <p>Sarah can observe and capture your wedding day in the background, quickly and quietly taking photojournalistic pictures rather than directing if you prefer. Or she can confidently play the role of Art Director and instruct beautiful poses. Either way, what is most important is that her clients are relaxed and having a really great time on their wedding day!</p>
  </div>
  <div class="col" style="left:194px;width:94px">
    <h4>Formal Photography</h4>
    <p>Many of Sarah's clients book her because of the easy-going approach she has. They can get on with having a great time on their day without worrying about formal photography. However, there are occasions when clients do want formal family pictures, and Sarah is more than happy to accommodate their requests.</p>
    <p>In order to keep the disruption on the day to a minimum, we recommend that Sarah photographs no more than 6 groups, and a select number of the special couple.</p>
  </div>
  <div class="col" style="left:297px;width:112px">
    <h4>Image Presentation</h4>
    <p>The most professional way of presenting clients with their photographs is in an elegantly designed photo book. Sarah's clients only pay one fixed price for the photography, regardless of how many images taken. There are no hard sell procedures to go through, and the completed book is prepared within 2-6 weeks after the wedding day.</p>
    <h4 class="later">Time of Year</h4>
    <p>Signature pictures can be taken on overcast days or winter months. Don't worry if the sky is not perfectly blue. In the end, regardless of the weather – it's the timeless mood of the day that Sarah strives to capture.</p>
  </div>
  <div class="photo rings" role="img" aria-label="Close-up of two wedding rings"></div>
  <div class="abs tab"></div>
  <div class="page-num">2</div>
</section>

<section class="page reviews">
  <div class="abs num-block"><span>3</span></div>
  <div class="tile" style="left:82px;top:16px;width:66px;height:62px" role="img" aria-label="Wedding guests"></div>
  <div class="tile" style="left:151px;top:16px;width:65px;height:62px" role="img" aria-label="Wedding invitation detail"></div>
  <div class="tile" style="left:219px;top:16px;width:65px;height:62px" role="img" aria-label="Bridal flowers"></div>
  <div class="tile" style="left:287px;top:16px;width:65px;height:62px" role="img" aria-label="Bouquet detail"></div>
  <div class="tile" style="left:355px;top:16px;width:67px;height:62px" role="img" aria-label="Wedding dress detail"></div>
  <div class="tile" style="left:14px;top:83px;width:64px;height:64px" role="img" aria-label="Bride with family"></div>
  <div class="tile" style="left:14px;top:151px;width:64px;height:64px" role="img" aria-label="Couple portrait"></div>
  <div class="tile" style="left:355px;top:83px;width:67px;height:64px" role="img" aria-label="Ceremony outdoors"></div>
  <div class="tile" style="left:355px;top:151px;width:67px;height:64px" role="img" aria-label="Guests in garden"></div>
  <div class="tile" style="left:14px;top:222px;width:64px;height:65px" role="img" aria-label="Reception moment"></div>
  <div class="tile" style="left:82px;top:222px;width:66px;height:65px" role="img" aria-label="Family embrace"></div>
  <div class="tile" style="left:151px;top:222px;width:65px;height:65px" role="img" aria-label="Group at building"></div>
  <div class="tile" style="left:219px;top:222px;width:65px;height:65px" role="img" aria-label="Bride in avenue of trees"></div>
  <div class="tile" style="left:287px;top:222px;width:65px;height:65px" role="img" aria-label="Couple walking"></div>
  <div class="tile" style="left:355px;top:222px;width:67px;height:65px" role="img" aria-label="Bridal party"></div>
  <div class="quote-panel">
    <h2>What client's are saying…</h2>
    <p>"Words can't express my thanks Sarah, I am absolutely in awe of my photos! You've captured my wedding day perfectly; couldn't ask for anything more."</p>
    <cite>– Tess, Kingsville</cite>
    <p>"Thanks so much for photographing our special day, you did an amazing job and made everyone feel so comfortable. The amount of comments we have had on the photos so far has been wonderful and we couldn't be happier!"</p>
    <cite>– Hannah, Footscray</cite>
  </div>
</section>

<section class="page packages">
  <div class="abs band">Wedding Packages</div>
  <div class="pkg" style="left:0">
    <div class="shot" role="img" aria-label="Couple under a willow tree"></div>
    <div class="label" style="background:var(--sage)">Signature</div>
    <div class="price">Price: $3680 ($5540 value)</div>
    <div class="cover-hrs">Up to 8 hrs of coverage</div>
    <ul>
      <li>Signature Grand (A3) Album with Lay-flat 300g paper, frosted page, choice of premium linen or leather cover, presentation box, name embossing, up to 52 pages</li>
      <li class="accent">Custom Thank-you Cards with envelopes (50)</li>
      <li>Client for life (no sitting fees)</li>
      <li>Second photographer</li>
      <li>Fusion Slideshow (still + moving images)</li>
      <li>Pre-wedding Shoot</li>
      <li>Web Gallery (online for 6 weeks) &amp; Social media</li>
      <li>High Resolution Digital Negatives*</li>
    </ul>
  </div>
  <div class="pkg" style="left:146px">
    <div class="shot" role="img" aria-label="Couple on a tree-lined road"></div>
    <div class="label" style="background:var(--mint)">Platinum</div>
    <div class="price">Price: $2300 ($3440 value)</div>
    <div class="cover-hrs">Up to 6 hrs of coverage</div>
    <ul>
      <li>Regular (A4) Album with Lay-flat 300g paper, printed cover, dust jacket, presentation box, up to 42 pages</li>
      <li>Slideshow</li>
      <li>Pre-wedding shoot</li>
      <li>Web Gallery (online for 6 weeks) &amp; Social media</li>
      <li>High Resolution Digital Negatives*</li>
    </ul>
  </div>
  <div class="pkg" style="left:292px">
    <div class="shot" role="img" aria-label="Bride and groom by a stone church"></div>
    <div class="label" style="background:var(--mint-pale)">Gold</div>
    <div class="price">Price: $1650 ($2080 value)</div>
    <div class="cover-hrs">Up to 4 hrs of coverage</div>
    <ul>
      <li>Regular (A4) Album with Lay-flat 300g paper, printed cover, dust jacket, presentation box, up to 32 pages</li>
      <li>Web Gallery (online for 6 weeks) &amp; Social media</li>
      <li>High Resolution Digital Negatives*</li>
    </ul>
  </div>
  <div class="abs note">* Approx. 1200x1800 px at 240 ppi per inch. Suitable for prints up to 8x10 inch. No watermarks</div>
  <div class="page-num">4</div>
</section>

<section class="page extras">
  <div class="page-num">5</div>
  <div class="fee-list">
    <div class="item">Engagement Session/Pre-wedding Shoot</div>
    <div>$290 for up to 2 hours of photography on location</div>
    <div class="item">Digital Negatives</div>
    <div>$490</div>
    <div class="item">Extended Coverage</div>
    <div>$160 per hour</div>
    <div class="item">Web Gallery &amp; Social media posting</div>
    <div>$140</div>
    <div class="item">Slideshow</div>
    <div>$250</div>
    <div class="item">Second Photographer</div>
    <div>$590</div>
    <div class="item">Client for life</div>
    <div>No sitting fees for portrait sessions – Anniversaries, family portraits, etc: $390</div>
    <div class="item">Photo Enlargements</div>
    <div>Quality custom archival prints in a variety of sizes 5x7 up to 8x10 $25, 12.6x18.5 $40</div>
    <div class="gap">Stretched Canvas Prints for your wall. Various sizes available from 16"x20" starting at $395 through to 40"x60" $1500</div>
    <div class="gap">Plus many other options!</div>
    <div class="item">Professionally Edited Album (Regular)</div>
    <div>$790</div>
    <div class="item">Album Upgrade from Regular to Signature Grand</div>
    <div>From Gold Package to Signature Grand: $1150</div>
    <div>From Platinum Package to Signature Grand: $650</div>
    <div class="item">Custom Thank-you Cards</div>
    <div>$150 for 50 cards (174mm x 123mm) including envelopes</div>
  </div>
  <div class="photo bouquet" role="img" aria-label="Pink and cream rose bouquet in a glass jar"></div>
  <div class="abs label">À la Carte Fees to Consider</div>
</section>

<section class="page contact">
  <div class="photo still" role="img" aria-label="Black and white still life of bridal shoes beneath a chandelier lamp"></div>
  <h2 class="abs">How do you want to remember<br>your special day</h2>
  <div class="abs copy">
    <p>Elegant, stunning, fuss-free photography that doesn't cost the earth will capture those memories for a lifetime!</p>
    <p>Wedding photography packages start from $1650 and are fully inclusive of fun-filled creative &amp; journalistic coverage, digital negatives and professionally edited album.</p>
    <p>Contact Sarah today to arrange an informal catch-up, discuss your requirements and find out more about the early booking bonus!</p>
  </div>
  <div class="abs details">
    <div>Marlow Street, Seddon, VIC, 3011</div>
    <div class="url">www.sarahkelbrin.com</div>
    <div>Email: sarah@sarahkelbrin.com</div>
    <div>Mobile: 0400 555 218</div>
  </div>
  <div class="abs mark"></div>
  <div class="abs brand">Sarah Kelbrin</div>
</section>

</body>
</html>
```